Summit Bodyform Gym Website

We need a website design for our gym.

Summit is the UAE's first calisthenics and parkour gym. The theme under which the gym revolves is that one does not require any machinery to workout as our bodies could be themselves the machinery. The gym is designed to be the more of a social hub rather than an "in-and-out" gym, where people come train, have fun, hang out and socialize for a few hours rather than just train for 60 minutes then leave. The gym is designed to be a big open space with lots of natural sunlight, natural wood and plants all over the place to create a natural and refreshing setting. We also use recycled material throughout the gym and recycle our waste as being green is part of our philosophy. We currently also have some of the world's top and most recognized calisthenics athletes working with us.

We would like our website to reflect all that as well as provide a simple, interactive and fun way for visitors to be able to get class and gym information, check out gym media and contact us for bookings.

Target Market(s)

Ages 15-35

Industry/Entity Type

Fitness

Coding

Coded - Design and coding required

Number of Pages Required

4 page

Font styles to use
Decorative

Colors
0792cd

Requirements
Must have
• Class descriptions
• Gym description
• Class schedules
• Trainer profiles
• Gym philosophy
• Contact Details
Nice to have
• A link to contact us directly for a free first trial class

```html
<!DOCTYPE html>
<html lang="en">
<head>
<meta charset="utf-8">
<title>Summit Bodyform Gym</title>
<link rel="stylesheet" href="https://fonts.googleapis.com/css2?family=Roboto:wght@300;400;500;700&family=Roboto+Condensed:wght@400;700&family=Montserrat:wght@600;700;900&display=swap">
<style>
:root{
  --blue:#0792cd;
  --band:#0a9ec8;
  --ink:#222;
  --muted:#8a8f99;
  --pale:#eef0f4;
  --line:#dfe2e8;
  --green:#8cc63f;
  --dark:#23222a;
  --white:#fff;
}
*{box-sizing:border-box;margin:0;padding:0}
html,body{width:1200px;height:3125px;overflow:hidden}
body{font-family:"Roboto",sans-serif;color:var(--ink);background:var(--white);position:relative}
section,header,footer{position:relative;width:1200px}
.section-title{font-family:"Montserrat",sans-serif;font-weight:700;color:var(--blue);font-size:38px;text-align:center;letter-spacing:.5px}

/* header */
.site-header{height:598px}
.hero-photo{position:absolute;inset:0;background:linear-gradient(110deg,#cfdbe6 0%,#eef3f8 35%,#9fb6cc 60%,#dfe8f0 100%)}
.topbar{position:absolute;top:0;left:0;width:1200px;height:69px;background:var(--band)}
.brand{position:absolute;left:0;top:0;width:222px;height:96px;background:var(--white);display:flex;align-items:center;justify-content:center;gap:10px}
.brand-dot{width:16px;height:16px;border-radius:50%;background:var(--blue)}
.brand-name{font-family:"Montserrat",sans-serif;font-weight:700;font-size:26px;color:var(--blue)}
.main-nav{position:absolute;left:312px;top:0;width:888px;height:69px;display:flex}
.main-nav a{flex:1 1 auto;display:flex;align-items:center;justify-content:center;height:69px;padding:0 14px;color:var(--white);font-family:"Montserrat",sans-serif;font-weight:700;font-size:14px;white-space:nowrap;text-decoration:none;border-left:1px solid rgba(255,255,255,.25)}
.main-nav a.active{background:rgba(255,255,255,.12)}

/* description */
.gym-description{height:402px}
.gym-description h2{position:absolute;left:56px;top:44px;font-family:"Montserrat",sans-serif;font-weight:700;font-size:40px;color:var(--blue)}
.lead{position:absolute;left:56px;top:104px;color:var(--blue);font-weight:500;font-size:15px}
.desc-body{position:absolute;left:56px;top:146px;width:610px;font-size:15px;line-height:23px;color:#333}
.desc-body p{margin-bottom:23px}
.bench-photo{position:absolute;left:708px;top:52px;width:396px;height:342px;background:radial-gradient(ellipse at center,#b9bec6 0%,#e7e9ec 55%,#fff 75%)}

/* cta */
.cta-band{height:185px;background:var(--band)}
.cta-band p{position:absolute;left:129px;top:46px;width:560px;color:var(--white);font-weight:300;font-size:34px;line-height:42px}
.btn-outline{position:absolute;left:806px;top:58px;width:202px;height:67px;border:2px solid var(--white);border-radius:8px;color:var(--white);display:flex;align-items:center;justify-content:center;font-size:28px;font-weight:300}

/* schedules */
.class-schedules{height:640px;background:var(--pale)}
.class-schedules .section-title{padding-top:36px}
.day-tabs{position:absolute;left:202px;top:109px;width:798px;height:37px;background:var(--white);border-radius:19px;display:flex;justify-content:space-between;align-items:center;padding-right:20px}
.day-tabs span{font-family:"Roboto Condensed",sans-serif;font-size:14px;font-weight:700;color:var(--muted);width:108px;text-align:center}
.day-tabs span.active{background:var(--green);color:var(--white);height:37px;line-height:37px;border-radius:19px;width:106px}
.class-grid{position:absolute;left:52px;top:196px;width:1094px;display:grid;grid-template-columns:repeat(4,1fr);grid-template-rows:202px 200px}
.class-card{border-right:1px solid var(--line);border-bottom:1px solid var(--line);display:flex;flex-direction:column;align-items:center;padding-top:22px}
.class-card:nth-child(4n){border-right:none}
.class-card:nth-child(n+5){border-bottom:none}
.class-card svg{width:46px;height:46px;stroke:var(--blue);fill:none;stroke-width:2.2}
.time-pill{margin-top:14px;background:#3aaee0;color:var(--white);font-family:"Roboto Condensed",sans-serif;font-weight:700;font-size:13px;padding:4px 14px;border-radius:12px}
.class-card h3{margin-top:14px;font-family:"Roboto Condensed",sans-serif;font-weight:400;font-size:20px;color:#222}
.class-card .coach{margin-top:6px;font-family:"Roboto Condensed",sans-serif;font-size:13px;color:var(--muted)}

/* trainers */
.trainer-profiles{height:567px}
.trainer-profiles .section-title{padding-top:34px}
.team-photo{position:absolute;left:0;top:102px;width:330px;height:465px;background:linear-gradient(160deg,#d9c2aa 0%,#8a6d55 45%,#2a2a2a 80%)}
.team-claim{position:absolute;left:304px;top:236px;width:250px;font-family:"Montserrat",sans-serif;font-weight:900;color:#111;line-height:1}
.team-claim span{display:block;font-size:29px;line-height:34px;letter-spacing:-.3px}
.team-claim strong{display:block;font-size:66px;line-height:66px;font-weight:900;letter-spacing:-1px}
.btn-pill{position:absolute;left:312px;top:410px;width:150px;height:40px;background:#3d8fd1;border-radius:20px;color:var(--white);font-family:"Montserrat",sans-serif;font-weight:700;font-size:11px;display:flex;align-items:center;justify-content:center}
.group-head{position:absolute;left:587px;top:127px;font-family:"Montserrat",sans-serif;font-weight:700;font-size:16px;line-height:20px}
.group-text{position:absolute;left:587px;top:180px;width:548px;font-size:11px;line-height:17px;color:var(--muted)}
.slider-dots{position:absolute;left:1096px;top:152px;display:flex;gap:6px}
.slider-dots i{width:9px;height:9px;border-radius:50%;background:#999}
.slider-dots i.on{background:var(--green)}
.trainer-card{position:absolute;top:243px;width:263px;height:255px;background:#f0f1f4}
.trainer-card .photo{height:188px}
.trainer-card .plus{position:absolute;right:14px;top:175px;width:26px;height:26px;border-radius:50%;background:#5a6ad8;color:#fff;font-size:18px;line-height:26px;text-align:center}
.trainer-card h4{margin:20px 0 0 17px;font-family:"Roboto Condensed",sans-serif;font-weight:400;font-size:14px}
.trainer-card small{display:block;margin:4px 0 0 17px;font-family:"Roboto Condensed",sans-serif;font-size:10px;color:var(--muted)}

/* philosophy */
.gym-philosophy{height:404px;background:var(--dark)}
.gym-philosophy h2{position:absolute;left:58px;top:56px;font-family:"Montserrat",sans-serif;font-weight:700;font-size:38px;color:var(--blue)}
.story-title{position:absolute;left:66px;top:132px;font-family:"Roboto Condensed",sans-serif;font-weight:400;font-size:20px;color:#9acd32}
.story-body{position:absolute;left:66px;top:180px;width:380px;font-size:12px;line-height:22px;color:#b8b9c0}
.story-body p{margin-bottom:22px}
.gym-philosophy .slider-dots{left:66px;top:322px}
.gym-philosophy .slider-dots i{background:#777}
.gym-philosophy .slider-dots i.on{background:#fff}
.athlete-photo{position:absolute;left:525px;top:0;width:675px;height:404px;background:linear-gradient(90deg,#3b3a3e 0%,#7a6a5e 45%,#3a3a3c 100%)}

/* footer */
.site-footer{height:329px;background:var(--band);color:var(--white);text-align:center}
.footer-brand{position:absolute;left:0;right:0;top:66px;display:flex;justify-content:center;align-items:center;gap:12px}
.footer-brand .brand-dot{background:var(--white)}
.footer-brand .brand-name{color:var(--white);font-size:34px}
.footer-text{position:absolute;left:0;right:0;top:170px;font-size:15px}
.copyright{position:absolute;left:0;right:0;top:214px;font-size:15px}
.social{position:absolute;left:0;right:0;top:262px;display:flex;justify-content:center;gap:18px}
.social span{width:28px;height:28px;background:#3f3f44;transform:rotate(45deg);margin:6px}
</style>
</head>
<body>

<header class="site-header">
  <div class="hero-photo" role="img" aria-label="Photo of a man training on a cable machine in a bright gym"></div>
  <div class="topbar"></div>
  <div class="brand"><span class="brand-dot"></span><span class="brand-name">Summit</span></div>
  <nav class="main-nav">
    <a class="active">HOME</a><a>ABOUT US</a><a>CLASSES</a><a>TRAINERS</a><a>EVENT</a><a>ELEMENTS</a><a>SHOP</a><a>CONTACT</a>
  </nav>
</header>

<section class="gym-description">
  <h2>GYM DESCRIPTION</h2>
  <p class="lead">Lorem ipsum dolor sit amet, consectetuer adipiscing elit.</p>
  <div class="desc-body">
    <p>Aenean commodo ligula eget dolor. Aenean massa. Cum sociis natoque penatibus et magnis dis parturient montes, nascetur ridiculus mus. Donec quam felis, ultricies nec, pellentesque eu, pretium quis, sem.</p>
    <p>Phasellus dignissim arcu neque, non porta leo molestie eu. Nam id condimentum lectus. Proin placerat sed urna nec convallis. Morbi vitae odio congue, laoreet risus ut, commodo sapien. Aenean massa. Cum sociis natoque penatibus et magnis</p>
    <p>Phasellus dignissim arcu neque, non porta leo molestie eu. Nam id.</p>
  </div>
  <div class="bench-photo" role="img" aria-label="Photo of a man doing a barbell bench press"></div>
</section>

<section class="cta-band">
  <p>Choose Your Classes and Start Your Training</p>
  <a class="btn-outline">Book Now</a>
</section>

<section class="class-schedules">
  <h2 class="section-title">CLASS SCHEDULES</h2>
  <div class="day-tabs">
    <span class="active">MONDAY</span><span>TUESDAY</span><span>WEDNESDAY</span><span>THURSDAY</span><span>FRIDAY</span><span>SATURDAY</span><span>SUNDAY</span>
  </div>
  <div class="class-grid">
    <div class="class-card">
      <svg viewBox="0 0 46 46"><circle cx="24" cy="8" r="4"/><path d="M24 13v14l-8 8M24 20l8 6M8 40h30"/></svg>
      <span class="time-pill">06AM-8AM</span><h3>WEIGHT LOOSE PROGRAM</h3><span class="coach">OMAR HADDAD</span>
    </div>
    <div class="class-card">
      <svg viewBox="0 0 46 46"><path d="M23 40C8 28 4 20 8 13c4-6 11-5 15 1 4-6 11-7 15-1 4 7 0 15-15 27z"/><path d="M6 24h10l3-6 4 10 3-4h14"/></svg>
      <span class="time-pill">08AM-10AM</span><h3>CARDIO PROGRAM</h3><span class="coach">RAFAEL MENDES</span>
    </div>
    <div class="class-card">
      <svg viewBox="0 0 46 46"><circle cx="12" cy="14" r="3"/><path d="M6 22l8 4 6-6 6 10 6-6 8 4M10 34h28"/></svg>
      <span class="time-pill">10AM-01PM</span><h3>YOGA CLASSES</h3><span class="coach">LENA VARGA</span>
    </div>
    <div class="class-card">
      <svg viewBox="0 0 46 46"><rect x="6" y="22" width="34" height="12" rx="3"/><path d="M12 22v-6M18 22v-8M24 22v-8M30 22v-8M36 22v-6"/></svg>
      <span class="time-pill">01PM-02PM</span><h3>FITNESS PROGRAM</h3><span class="coach">OMAR HADDAD</span>
    </div>
    <div class="class-card">
      <svg viewBox="0 0 46 46"><path d="M16 6h14l10 8-5 6-4-3v23H15V17l-4 3-5-6z"/><path d="M15 26h16"/></svg>
      <span class="time-pill">04PM-06PM</span><h3>KARATE CLASSES</h3><span class="coach">KARIM NASSER</span>
    </div>
    <div class="class-card">
      <svg viewBox="0 0 46 46"><path d="M14 8h16a6 6 0 0 1 6 6v14H12V10z"/><rect x="14" y="28" width="20" height="10" rx="2"/></svg>
      <span class="time-pill">06PM-07PM</span><h3>BOXING PROGRAM</h3><span class="coach">THEO BRANDT</span>
    </div>
    <div class="class-card">
      <svg viewBox="0 0 46 46"><circle cx="22" cy="26" r="12"/><path d="M22 14V8h8M22 26l5-5"/></svg>
      <span class="time-pill">07PM-08PM</span><h3>AEROBICS &amp; SKIPPING</h3><span class="coach">SAMI OKAFOR</span>
    </div>
    <div class="class-card">
      <svg viewBox="0 0 46 46"><rect x="6" y="16" width="8" height="14" rx="2"/><rect x="32" y="16" width="8" height="14" rx="2"/><path d="M14 23h18M3 23h3M40 23h3"/></svg>
      <span class="time-pill">08PM-09PM</span><h3>BODY BUILDING</h3><span class="coach">DARIO COSTA</span>
    </div>
  </div>
</section>

<section class="trainer-profiles">
  <h2 class="section-title">TRAINER PROFILES</h2>
  <div class="team-photo" role="img" aria-label="Photo of a male and a female trainer in sportswear"></div>
  <div class="team-claim"><span>WELL</span><span>EXPERIENCED</span><strong>TEAM</strong></div>
  <a class="btn-pill">VIEW THE TEAM</a>
  <div class="group-head">GROUP OF<br>EXPERIENCED TRAINERS</div>
  <div class="slider-dots"><i></i><i></i><i class="on"></i></div>
  <p class="group-text">Lorem ipsum dolor sit amet, consectetur adipiscing elit. Cras ut nunc sapien. Pellentesque feugiat risus nec fringilla dolor pellentesque aliquet. Cras eget odio a massa viverra.</p>
  <div class="trainer-card" style="left:587px">
    <div class="photo" role="img" aria-label="Photo of a muscular trainer on gymnastic rings" style="background:linear-gradient(90deg,#4a4a4a 0%,#c9d92a 60%,#e4ee3a 100%)"></div>
    <span class="plus">+</span><h4>YUSUF RAHMAN</h4><small>BODY BUILDING TRAINER</small>
  </div>
  <div class="trainer-card" style="left:873px">
    <div class="photo" role="img" aria-label="Photo of a fitness trainer coaching a woman lifting a barbell" style="background:linear-gradient(90deg,#6b6f78 0%,#c8b8a8 50%,#b23a3a 100%)"></div>
    <span class="plus">+</span><h4>ELIAS MOREAU</h4><small>FITNESS TRAINER</small>
  </div>
</section>

<section class="gym-philosophy">
  <h2>GYM PHILOSOPHY</h2>
  <h3 class="story-title">LENA LOOSE 30 LBS IN 2 MONTHS</h3>
  <div class="story-body">
    <p>In pellentesque faucibus vestibulum. Nulla at nulla justo, eget luc in blandit. Curabitur vulputate, ligula lacinia scelerisque tempor augue sit amet leo consequat. Loosing Great.</p>
    <p>In pellentesque faucibus vestibulum. Nulla at nulla justo, eget luc in blandit. Curabitur vulputate, ligula lacinia.</p>
  </div>
  <div class="slider-dots"><i></i><i></i><i class="on"></i></div>
  <div class="athlete-photo" role="img" aria-label="Photo of a woman doing a pull-up in a dark gym"></div>
</section>

<footer class="site-footer">
  <div class="footer-brand"><span class="brand-dot"></span><span class="brand-name">Summit</span></div>
  <p class="footer-text">Lorem ipsum dolor sit amet, consectetur adipiscing elit, sed do eiusmod tempor incididunt ut labore et dolore magna ali qua.</p>
  <p class="copyright">Copyright © Summit 2015. All rights reserved.</p>
  <div class="social"><span></span><span></span><span></span><span></span></div>
</footer>

</body>
</html>
```